Retail swing tag labels for a sale / reduction

We need some graphics done to be made into retail swing tag labels, for the purpose of reductions on selected products.

We have attached 2 examples of previous designs that were similar idea, but more themed for 'autumn' and 'winter'. This theme will just have the word 'REDUCED'.

The white areas can be smaller in size, as we would like to include a large "20% OFF" at the bottom, and then a 30%, 40%, 50% option.

Overall colour scheme should be red background with some form of detailed patterning (see previous examples). Bright and e-catching.

Any other questions, just ask.

The screenshot is front the printers, but in horizontal orientation.

The finished dimensions will be A6 portrait, printed both sides.

We have also included the vector file of the shop "Hollowmere Furnishings", which can be included on 1 of the sides.

```html
<!DOCTYPE html>
<html lang="en">
<head>
<meta charset="utf-8">
<title>Reduced 20% Off – Swing Tag</title>
<link rel="stylesheet" href="https://fonts.googleapis.com/css2?family=Montserrat:wght@400;800;900&family=Oswald:wght@700&display=swap">
<style>
  :root {
    --tag-red: #e6232f;
    --tag-red-band: #d21c2e;
    --badge-ring: #f5c4b6;
    --badge-ring-edge: #e8937f;
    --badge-core: #ba141f;
    --badge-core-band: #a3131b;
    --ink-white: #ffffff;
    --trim-blue: #3b4fa8;
    --trim-green: #2f8a4a;
  }
  html, body {
    margin: 0;
    padding: 0;
    width: 859px;
    height: 1200px;
    overflow: hidden;
    background: var(--tag-red);
  }
  .swing-tag {
    display: block;
    width: 859px;
    height: 1200px;
  }
  .headline {
    font-family: "Montserrat", sans-serif;
    font-weight: 900;
    font-size: 138px;
    fill: var(--ink-white);
  }
  .discount-figure {
    font-family: "Oswald", sans-serif;
    font-weight: 700;
    font-size: 238px;
    fill: var(--ink-white);
  }
  .discount-label {
    font-family: "Montserrat", sans-serif;
    font-weight: 800;
    font-size: 104px;
    fill: var(--ink-white);
  }
  .brand-name {
    font-family: "Montserrat", sans-serif;
    font-weight: 400;
    font-size: 29px;
    fill: var(--ink-white);
  }
  .brand-mark {
    fill: none;
    stroke: var(--ink-white);
    stroke-width: 1.5;
  }
  .trim-line { fill: none; stroke-width: 1; }
  .trim-line--bleed { stroke: var(--trim-blue); }
  .trim-line--safe { stroke: var(--trim-green); }
</style>
</head>
<body>
<svg class="swing-tag" viewBox="0 0 859 1200" xmlns="http://www.w3.org/2000/svg">
  <defs>
    <pattern id="tagBands" x="0" y="0" width="859" height="106" patternUnits="userSpaceOnUse">
      <rect x="0" y="0" width="859" height="53" fill="var(--tag-red)"/>
      <rect x="0" y="53" width="859" height="53" fill="var(--tag-red-band)"/>
    </pattern>
    <pattern id="badgeBands" x="0" y="0" width="859" height="106" patternUnits="userSpaceOnUse">
      <rect x="0" y="0" width="859" height="53" fill="var(--badge-core)"/>
      <rect x="0" y="53" width="859" height="53" fill="var(--badge-core-band)"/>
    </pattern>
  </defs>

  <rect class="tag-background" x="0" y="0" width="859" height="1200" fill="url(#tagBands)"
        role="img" aria-label="Red background with a repeating geometric triangle pattern in alternating bands"/>

  <rect class="trim-line trim-line--bleed" x="12" y="12" width="835" height="1176"/>
  <rect class="trim-line trim-line--safe" x="23" y="23" width="813" height="1154"/>

  <text class="headline" x="432" y="272" text-anchor="middle" textLength="641" lengthAdjust="spacingAndGlyphs">REDUCED</text>

  <g class="discount-badge">
    <circle cx="429" cy="631" r="286" fill="var(--badge-ring-edge)"/>
    <circle cx="429" cy="631" r="276" fill="var(--badge-ring)"/>
    <circle cx="429" cy="631" r="246" fill="url(#badgeBands)"
            role="img" aria-label="Deep red badge centre with a faint triangle pattern"/>
    <text class="discount-figure" x="433" y="669" text-anchor="middle" textLength="386" lengthAdjust="spacingAndGlyphs">20%</text>
    <text class="discount-label" x="431" y="780" text-anchor="middle" textLength="211" lengthAdjust="spacingAndGlyphs">OFF</text>
  </g>

  <g class="brand">
    <rect class="brand-mark" x="345" y="946" width="125" height="96"/>
    <text class="brand-name" x="407" y="1085" text-anchor="middle" textLength="442" lengthAdjust="spacing">HOLLOWMERE FURNISHINGS</text>
  </g>
</svg>
</body>
</html>
```